Redesign of business card for Cedar Ridge Mechanical

We are looking for a new design for our business cards for Cedar Ridge Mechanical. We are a plumbing & HVAC construction company, operating on the West Coast of Canada and USA. Logo attached.
Industry/Entity Type
Construction - Plumbing & HVAC
Contact Information for Business Card
Name, address, phone numbers, email, website address
Look and feel
Each slider illustrates characteristics of the customer's brand and the style your logo design should communicate.

```html
<!DOCTYPE html>
<html lang="en">
<head>
<meta charset="utf-8">
<title>Cedar Ridge Mechanical – Business Card</title>
<link href="https://fonts.googleapis.com/css2?family=Montserrat:wght@400;700&display=swap" rel="stylesheet">
<style>
  :root {
    --bg: #141414;
    --card-dark: #232323;
    --card-light: #ffffff;
    --ink-dark: #232323;
    --ink-light: #ffffff;
    --ink-soft: #e6e6e6;
  }
  * { margin: 0; padding: 0; box-sizing: border-box; }
  html, body { width: 1200px; height: 1059px; overflow: hidden; background: var(--bg); }
  body { position: relative; font-family: "Montserrat", sans-serif; }

  .card {
    position: absolute;
    width: 693px;
    height: 393px;
    border-radius: 24px;
    overflow: hidden;
  }
  .card--front { left: 253px; top: 89px; background: var(--card-light); }
  .card--back  { left: 253px; top: 546px; background: var(--card-dark); }

  .front-wave { position: absolute; inset: 0; width: 100%; height: 100%; }

  .brand {
    position: absolute;
    display: flex;
    align-items: center;
    font-weight: 700;
    text-transform: uppercase;
    letter-spacing: 0.04em;
  }
  .brand__mark { flex: none; border-radius: 4px; }
  .brand__name { line-height: 1.15; }

  .brand--front { right: 34px; top: 46px; gap: 12px; color: var(--ink-dark); font-size: 17px; }
  .brand--front .brand__mark { width: 44px; height: 44px; background: var(--ink-dark); }

  .brand--back {
    left: 0; right: 0; top: 0; bottom: 0;
    justify-content: center;
    gap: 22px;
    color: var(--ink-light);
    font-size: 36px;
  }
  .brand--back .brand__mark { width: 84px; height: 84px; background: var(--ink-light); border-radius: 8px; }

  .contact { position: absolute; left: 29px; top: 158px; color: var(--ink-light); }
  .contact__name { font-weight: 700; font-size: 22px; letter-spacing: 0.02em; }
  .contact__title { font-size: 13.5px; color: var(--ink-soft); margin-top: 3px; letter-spacing: 0.02em; }
  .contact__address { font-size: 14px; line-height: 18px; color: var(--ink-soft); margin-top: 29px; }
  .contact__list { list-style: none; margin-top: 16px; }
  .contact__item { display: flex; align-items: center; gap: 12px; font-size: 14px; height: 27px; color: var(--ink-soft); }
  .contact__icon { width: 14px; height: 14px; fill: var(--ink-light); flex: none; }
</style>
</head>
<body>

<section class="card card--front" aria-label="Business card front">
  <svg class="front-wave" viewBox="0 0 693 393" preserveAspectRatio="none" aria-hidden="true">
    <path fill="var(--card-dark)" d="M0,128 C40,108 80,98 112,99 C230,100 300,210 420,218 C520,225 620,185 693,140 L693,393 L0,393 Z"/>
    <path fill="var(--card-light)" d="M200,113 C280,150 340,210 440,226 C540,240 620,212 693,190 L693,198 C620,225 540,252 440,244 C340,232 280,168 200,113 Z"/>
    <path fill="var(--card-light)" d="M295,200 C340,232 390,258 470,266 C560,272 630,250 693,222 L693,232 C630,264 560,286 470,279 C390,272 340,242 295,200 Z"/>
  </svg>

  <div class="brand brand--front">
    <span class="brand__mark" aria-hidden="true"></span>
    <span class="brand__name">Cedar Ridge<br>Mechanical</span>
  </div>

  <div class="contact">
    <h1 class="contact__name">Daniel Hayes</h1>
    <p class="contact__title">Managing Director</p>
    <p class="contact__address">240 Harbor View Road<br>Bellingham, WA 98225</p>
    <ul class="contact__list">
      <li class="contact__item">
        <svg class="contact__icon" viewBox="0 0 24 24" aria-hidden="true"><path d="M6.6 10.8a15.1 15.1 0 0 0 6.6 6.6l2.2-2.2c.3-.3.7-.4 1-.2 1.1.4 2.3.6 3.6.6.6 0 1 .4 1 1V20c0 .6-.4 1-1 1C10.6 21 3 13.4 3 4c0-.6.4-1 1-1h3.5c.6 0 1 .4 1 1 0 1.3.2 2.5.6 3.6.1.3 0 .7-.2 1z"/></svg>
        <span>555.204.7316</span>
      </li>
      <li class="contact__item">
        <svg class="contact__icon" viewBox="0 0 24 24" aria-hidden="true"><path d="M2 5h20v2l-10 6L2 7z M2 9l10 6 10-6v10H2z"/></svg>
        <span>info@cedarridgemech.com</span>
      </li>
      <li class="contact__item">
        <svg class="contact__icon" viewBox="0 0 24 24" aria-hidden="true"><circle cx="12" cy="12" r="10"/><path fill="var(--card-dark)" d="M7 7c2 0 3 1 3 3s-2 2-2 4-2 1-3 0c-1-2 0-7 2-7zm8 2c2 0 3 2 2 4s-3 3-4 5c-1 1-2 0-1-2 1-2 0-3 1-5 0-1 1-2 2-2z"/></svg>
        <span>www.cedarridgemech.com</span>
      </li>
    </ul>
  </div>
</section>

<section class="card card--back" aria-label="Business card back">
  <div class="brand brand--back">
    <span class="brand__mark" aria-hidden="true"></span>
    <span class="brand__name">Cedar Ridge<br>Mechanical</span>
  </div>
</section>

</body>
</html>
```